jQuery Mobile CSS for web app

Task Outline:
Create jQuery Mobile themeroller compliant CSS and icons for a mobile web app.
Task Description:
Brindle Solutions are in the process of implementing a new, web based version of their Tessel operations platform.
The web based version of Tessel is built on top of the jQuery Mobile platform and we are looking for a designer to create a jQuery Mobile themeroller compliant CSS theme pack that we can plug into our application. The aim is to remove the standard jQuery Mobile look and feel and to introduce the Brindle branding throughout the new web app.
A number of screenshots are shown in the attached design spec (brindle_solutions.pdf) that show what the current (Windows Mobile 6.5) application looks like, alongside the development version of our new web app.
Deliverables:
• jQuery Mobile (v 1.4.2) themeroller compliant CSS which provides theming for all jQuery Mobile UI components.
• Example html showing how to use the CSS theme (especially where additional html/css classes are required).
• New set of status icons (as listed in attachment)
Inspiration:
See our website for current branding: www.brindle-solutions-demo.net

```html
<!DOCTYPE html>
<html lang="en">
<head>
<meta charset="utf-8">
<title>Job Header</title>
<link href="https://fonts.googleapis.com/css2?family=Roboto:wght@400;500;700&display=swap" rel="stylesheet">
<style>
  :root {
    --bar-top: #3a3a3a;
    --bar-bottom: #141414;
    --bar-text: #ffffff;
    --body-bg: #eeeeef;
    --section-line: #c9c9cc;
    --section-highlight: #fafafa;
    --label: #333333;
    --field-bg: #ffffff;
    --field-border: #d9d9dc;
    --field-text: #666666;
    --select-btn-top: #5a5a5a;
    --select-btn-bottom: #2a2a2a;
    --accent-red: #e0353a;
    --filler-top: #cfcfcf;
    --filler-bottom: #c2c2c2;
    --footer-bg: #1c1c1c;
    --nav-btn-top: #737a83;
    --nav-btn-bottom: #3d434b;
    --menu-tile: #262626;
    --menu-bar-top: #bdbdbd;
    --menu-bar-bottom: #7a7a7a;
    --screen-code: #cccccc;
  }
  * { box-sizing: border-box; margin: 0; padding: 0; }
  html, body { width: 928px; height: 1200px; overflow: hidden; }
  body { font-family: "Roboto", Arial, sans-serif; background: var(--body-bg); position: relative; }

  .app-header {
    position: absolute; left: 0; top: 0; width: 928px; height: 132px;
    background: linear-gradient(var(--bar-top), var(--bar-bottom));
    display: flex; align-items: center; justify-content: center;
  }
  .app-header__title { color: var(--bar-text); font-size: 45px; font-weight: 500; }

  .form-section {
    position: absolute; left: 0; width: 928px;
    background: var(--body-bg);
    border-bottom: 3px solid var(--section-line);
    box-shadow: inset 0 3px 0 var(--section-highlight);
  }
  .form-section--customer { top: 132px; height: 240px; box-shadow: none; }
  .form-section--reference { top: 372px; height: 237px; }
  .form-section--description { top: 609px; height: 237px; }

  .field-label {
    position: absolute; left: 105px; font-size: 36px; color: var(--label);
  }
  .field {
    position: absolute; left: 103px; width: 722px; height: 98px;
    background: var(--field-bg); border: 2px solid var(--field-border);
    border-radius: 16px; box-shadow: inset 0 2px 4px rgba(0,0,0,0.06);
    font-size: 32px; color: var(--field-text);
    padding-left: 36px; display: flex; align-items: center;
  }
  .form-section--customer .field-label { top: 30px; }
  .form-section--customer .field { top: 105px; box-shadow: 0 3px 6px rgba(0,0,0,0.12); }
  .form-section--reference .field-label { top: 34px; }
  .form-section--reference .field { top: 100px; }
  .form-section--description .field-label { top: 37px; }
  .form-section--description .field { top: 103px; }

  .select-toggle {
    position: absolute; right: 14px; top: 14px; width: 62px; height: 64px;
    border-radius: 10px;
    background: linear-gradient(var(--select-btn-top), var(--select-btn-bottom));
    display: flex; align-items: center; justify-content: center;
  }

  .page-filler {
    position: absolute; left: 0; top: 846px; width: 928px; height: 195px;
    background: linear-gradient(var(--filler-top), var(--filler-bottom));
  }

  .app-footer {
    position: absolute; left: 0; top: 1041px; width: 928px; height: 159px;
    background: var(--footer-bg);
  }
  .nav-button {
    position: absolute; top: 37px; width: 206px; height: 82px;
  }
  .nav-button svg { position: absolute; inset: 0; }
  .nav-button__text {
    position: absolute; top: 0; height: 82px; display: flex; align-items: center;
    color: var(--bar-text); font-size: 40px; font-weight: 500;
  }
  .nav-button--back { left: 45px; }
  .nav-button--back .nav-button__text { left: 72px; }
  .nav-button--next { left: 667px; }
  .nav-button--next .nav-button__text { left: 50px; }

  .menu-toggle {
    position: absolute; left: 395px; top: 19px; width: 140px; height: 121px;
    background: var(--menu-tile);
    display: flex; flex-direction: column; align-items: center; justify-content: center; gap: 9px;
  }
  .menu-toggle__bar {
    width: 74px; height: 15px; border-radius: 2px;
    background: linear-gradient(var(--menu-bar-top), var(--menu-bar-bottom));
  }
  .screen-code {
    position: absolute; left: 880px; top: 127px; font-size: 28px; color: var(--screen-code);
  }
</style>
</head>
<body>
  <header class="app-header">
    <h1 class="app-header__title">Job Header</h1>
  </header>

  <section class="form-section form-section--customer">
    <label class="field-label">Customer Name : *</label>
    <div class="field field--select">one
      <span class="select-toggle">
        <svg width="34" height="30" viewBox="0 0 34 30" aria-hidden="true">
          <polygon points="2,3 32,3 17,27" fill="var(--accent-red)"/>
        </svg>
      </span>
    </div>
  </section>

  <section class="form-section form-section--reference">
    <label class="field-label">Customer Reference # :</label>
    <div class="field">two</div>
  </section>

  <section class="form-section form-section--description">
    <label class="field-label">Job Description :</label>
    <div class="field">three</div>
  </section>

  <div class="page-filler"></div>

  <footer class="app-footer">
    <div class="nav-button nav-button--back">
      <svg width="206" height="82" viewBox="0 0 206 82" aria-hidden="true">
        <defs>
          <linearGradient id="navFillBack" x1="0" y1="0" x2="0" y2="1">
            <stop offset="0" stop-color="var(--nav-btn-top)"/>
            <stop offset="1" stop-color="var(--nav-btn-bottom)"/>
          </linearGradient>
        </defs>
        <path d="M0,41 L38,0 H200 Q206,0 206,6 V76 Q206,82 200,82 H38 Z" fill="url(#navFillBack)"/>
      </svg>
      <span class="nav-button__text">Back</span>
    </div>

    <div class="menu-toggle" aria-label="Menu">
      <span class="menu-toggle__bar"></span>
      <span class="menu-toggle__bar"></span>
      <span class="menu-toggle__bar"></span>
    </div>

    <div class="nav-button nav-button--next">
      <svg width="206" height="82" viewBox="0 0 206 82" aria-hidden="true">
        <defs>
          <linearGradient id="navFillNext" x1="0" y1="0" x2="0" y2="1">
            <stop offset="0" stop-color="var(--nav-btn-top)"/>
            <stop offset="1" stop-color="var(--nav-btn-bottom)"/>
          </linearGradient>
        </defs>
        <path d="M206,41 L168,0 H6 Q0,0 0,6 V76 Q0,82 6,82 H168 Z" fill="url(#navFillNext)"/>
      </svg>
      <span class="nav-button__text">Next</span>
    </div>

    <span class="screen-code">C6</span>
  </footer>
</body>
</html>
```